wealth management firm, professional group, new model

we have a logo that works but we need a card, white background using our colors...clean look

our tag line if can be used in

Steady Guidance, Lasting Ownership

```html
<!DOCTYPE html>
<html lang="en">
<head>
<meta charset="utf-8">
<title>Arcova Capital Group — Business Card</title>
<link href="https://fonts.googleapis.com/css2?family=Montserrat:wght@400;500;700&display=swap" rel="stylesheet">
<style>
  :root {
    --backdrop: #d8dbdb;
    --card: #fbfbfa;
    --ink: #17233a;
    --ink-soft: #34405a;
    --edge: #1e3476;
  }
  * { box-sizing: border-box; margin: 0; padding: 0; }
  html, body {
    width: 1200px; height: 829px; overflow: hidden;
    background: var(--backdrop);
    font-family: "Montserrat", sans-serif;
    color: var(--ink);
  }
  .sheet {
    position: relative; width: 1200px; height: 829px;
    display: flex; align-items: center; justify-content: center; gap: 60px;
  }
  .card {
    position: relative;
    width: 500px; height: 286px;
    background: var(--card);
    border-bottom: 4px solid var(--edge);
    box-shadow: 0 6px 18px rgba(0,0,0,0.12);
  }
  .brand-name {
    display: flex; align-items: center; justify-content: center; gap: 12px;
    font-weight: 500; color: var(--ink); letter-spacing: 0.01em; white-space: nowrap;
  }
  .brand-name__mark { display: block; background: var(--ink); border-radius: 50%; flex: none; }

  /* Front: contact side */
  .card--contact .brand-name { position: absolute; top: 52px; left: 0; right: 0; font-size: 28px; }
  .card--contact .brand-name__mark { width: 14px; height: 14px; }
  .contact {
    position: absolute; top: 140px; left: 0; right: 0;
    display: flex; justify-content: center; align-items: center;
  }
  .person { text-align: right; padding-right: 20px; }
  .person__name { font-weight: 700; font-size: 17px; letter-spacing: 0.02em; text-transform: uppercase; }
  .person__title { font-size: 12px; color: var(--ink-soft); margin-top: 2px; }
  .divider { width: 1px; height: 62px; background: var(--ink-soft); }
  .channels { list-style: none; padding-left: 16px; font-size: 12.5px; }
  .channels li { display: flex; align-items: center; gap: 7px; line-height: 20px; }
  .channels svg { width: 11px; height: 11px; fill: var(--ink); flex: none; }
  .address {
    position: absolute; bottom: 28px; left: 0; right: 0;
    text-align: center; font-size: 12.5px;
  }

  /* Back: brand side */
  .card--brand { display: flex; flex-direction: column; align-items: center; justify-content: center; }
  .card--brand .brand-name { font-size: 36px; }
  .card--brand .brand-name__mark { width: 18px; height: 18px; }
  .tagline { margin-top: 22px; font-size: 14px; letter-spacing: 0.04em; color: var(--ink-soft); }
</style>
</head>
<body>
  <main class="sheet">
    <section class="card card--contact">
      <p class="brand-name"><span class="brand-name__mark"></span>Arcova Capital Group</p>
      <div class="contact">
        <div class="person">
          <p class="person__name">Daniel Whitford</p>
          <p class="person__title">CEO/Founder</p>
        </div>
        <div class="divider"></div>
        <ul class="channels">
          <li>
            <svg viewBox="0 0 16 16" aria-hidden="true"><path d="M3.6 1.2l2.3 2.6-1.3 1.8c.9 2 2.4 3.5 4.4 4.4l1.8-1.3 2.6 2.3-1.2 2.2C6.7 15 1 9.3 1.4 2.4z"/></svg>
            555-014-2278
          </li>
          <li>
            <svg viewBox="0 0 16 16" aria-hidden="true"><path d="M1 3h14v10H1zM2 4.2v.4l6 4 6-4v-.4z" fill-rule="evenodd"/></svg>
            hello@arcovacapital.com
          </li>
          <li>
            <svg viewBox="0 0 16 16" aria-hidden="true"><circle cx="8" cy="8" r="7"/></svg>
            www.arcovacapital.com
          </li>
        </ul>
      </div>
      <p class="address">450 Harbor Lane, Suite 210 Riverton, FL 32000</p>
    </section>

    <section class="card card--brand">
      <p class="brand-name"><span class="brand-name__mark"></span>Arcova Capital Group</p>
      <p class="tagline">Steady Guidance, Lasting Ownership</p>
    </section>
  </main>
</body>
</html>
```